Brindle Barks Chews Pouch Design

I want a pouch design for my yak cheese dog chews. My competitor is kindly tail, see attached. I want something minimalist like that where you see that there is only 3 ingredients, Yak milk, lime juice, Himalayan salt. I want it to say 100% natural 100% organic on it. Also odor free. There has to be a big see through window on it so you can see the products inside. Here is my logo and my competitor package. The package is 13cm x 17cm x 5cm. I have 5 sizes of bags to create but same image design
Updates

Target Market(s)

Pet owners

Industry/Entity Type

Dog products

Requirements
Must have
• « SMALL » « MIN NET WT 200 g / 5 PCS » and its important the 3 ingredients mentioned and 100% natural and organic must be very visible however the window must be big
Should not have
• The ingredients in the back

```html
<!DOCTYPE html>
<html lang="en">
<head>
<meta charset="utf-8">
<title>Brindle Barks Chews – Pouch Front</title>
<link rel="stylesheet" href="https://fonts.googleapis.com/css2?family=Fredoka:wght@600&family=Amatic+SC:wght@700&display=swap">
<style>
  :root {
    --backdrop: #ffd21a;
    --pouch-tan: #dcb372;
    --pouch-tan-light: #e6c48c;
    --tab-orange: #eaa43a;
    --band-cream: #f1ead0;
    --band-orange: #d9642a;
    --text-brown: #8a5a3a;
    --text-cream: #f4efd8;
    --ingredients-panel: #efa637;
    --ingredients-label: #cf5f2c;
    --window-light: #f4f3f0;
    --window-shade: #dcdad6;
    --mascot-sky: #6fb6c6;
    --mascot-fur: #d98a33;
    --logo-plate: #8a3b2b;
  }
  * { margin: 0; padding: 0; box-sizing: border-box; }
  html, body { width: 1200px; height: 1200px; overflow: hidden; }
  body { background: var(--backdrop); position: relative; }

  .pouch {
    position: absolute; left: 277px; top: 105px;
    width: 646px; height: 990px;
    background: var(--pouch-tan);
    border-radius: 14px;
    overflow: hidden;
  }
  .pattern-field {
    position: absolute; inset: 0;
    background: linear-gradient(180deg, var(--pouch-tan-light), var(--pouch-tan));
  }
  .odor-tab {
    position: absolute; left: 25px; top: 152px;
    width: 62px; height: 180px;
    background: var(--tab-orange);
    display: flex; align-items: center; justify-content: center;
  }
  .odor-tab span {
    writing-mode: vertical-rl;
    font-family: "Amatic SC", cursive;
    font-weight: 700; font-size: 44px; letter-spacing: 1px;
    color: var(--text-cream);
    white-space: nowrap;
  }
  .claim-band {
    position: absolute;
    display: flex; align-items: center; justify-content: center;
    font-family: "Fredoka", sans-serif; font-weight: 600;
    font-size: 50px; letter-spacing: 2px;
    white-space: nowrap;
  }
  .claim-natural {
    left: 143px; top: 149px; width: 503px; height: 87px;
    background: var(--band-cream); color: var(--text-brown);
  }
  .claim-organic {
    left: 146px; top: 252px; width: 466px; height: 84px;
    background: var(--band-orange); color: var(--text-cream);
  }
  .product-window {
    position: absolute; left: 25px; top: 332px;
    width: 596px; height: 300px;
    background: linear-gradient(170deg, var(--window-light) 0%, #ffffff 45%, var(--window-shade) 100%);
  }
  .window-upper {
    position: absolute; left: 87px; top: 317px;
    width: 534px; height: 20px;
    background: var(--window-light);
  }
  .ingredients-panel {
    position: absolute; left: 270px; top: 625px;
    width: 340px; height: 295px;
    background: var(--ingredients-panel);
    padding: 22px 0 0 14px;
  }
  .ingredients-label {
    font-family: "Fredoka", sans-serif; font-weight: 600;
    font-size: 20px; letter-spacing: 2px;
    color: var(--ingredients-label);
    text-align: center; margin-bottom: 8px;
    white-space: nowrap;
  }
  .ingredient-list { list-style: none; }
  .ingredient-list li {
    font-family: "Amatic SC", cursive; font-weight: 700;
    color: var(--text-cream); line-height: 1;
    white-space: nowrap;
  }
  .ingredient-list .big { font-size: 78px; }
  .ingredient-list .mid { font-size: 56px; }
  .brand-mark {
    position: absolute; left: 52px; top: 622px;
    width: 212px; height: 300px;
  }
  .mascot-art {
    position: absolute; left: 6px; top: 0;
    width: 200px; height: 200px; border-radius: 50%;
    background: radial-gradient(circle at 55% 45%, var(--mascot-fur) 0 45%, var(--mascot-sky) 46% 100%);
  }
  .brand-name {
    position: absolute; left: 0; right: 0; top: 214px;
    text-align: center;
    font-family: "Fredoka", sans-serif; font-weight: 600;
    font-size: 26px; line-height: 1.1;
    color: var(--logo-plate);
    white-space: nowrap;
  }
</style>
</head>
<body>
  <div class="pouch">
    <div class="pattern-field" role="img" aria-label="Faint repeating brand mascot pattern on tan pouch"></div>

    <div class="window-upper"></div>
    <div class="product-window" role="img" aria-label="Clear see-through window showing the chews inside"></div>

    <div class="odor-tab"><span>ODOR FREE</span></div>
    <div class="claim-band claim-natural">100% NATURAL</div>
    <div class="claim-band claim-organic">100%ORGANIC</div>

    <div class="brand-mark">
      <div class="mascot-art" role="img" aria-label="Round mascot illustration of a horned shaggy animal with mountains and sun"></div>
      <p class="brand-name">BRINDLE BARKS<br>CHEWS</p>
    </div>

    <div class="ingredients-panel">
      <p class="ingredients-label">3 INGREDIENTS</p>
      <ul class="ingredient-list">
        <li class="big">YALK MILK</li>
        <li class="mid">HIMALAYAN SALT</li>
        <li class="big">LIME JUICE</li>
      </ul>
    </div>
  </div>
</body>
</html>
```